Business Card for a mobile physiotherapy company

I need a layout for a business card for a mobile physiotherapy company.
Slogan is "Mobile Physiotherapy - Your Road To Recovery"
Phone number is 867-555-0142
Email VardenTherapy@postnest.ca (subject to change with website)
Website www.VardenTherapy.ca
My name and credentials: Luke Varden Luke Varden, BSc(kin), MPT, CAFCI, IMS
Information maybe included: Direct Billing, Services including Physiotherapy, IMS, acupuncture
Maybe include facebook and instagram logos
One side with the logo clean and sharp
Other side with details, try not to look too busy, keep everything concise

```html
<!DOCTYPE html>
<html lang="en">
<head>
<meta charset="utf-8">
<title>Varden Therapy – Business Card</title>
<link href="https://fonts.googleapis.com/css2?family=Roboto:wght@400;500;700&display=swap" rel="stylesheet">
<style>
  :root {
    --page-bg: #dedede;
    --teal-deep: #135a50;
    --teal-mid: #2c6878;
    --navy-blue: #2a5283;
    --brand-blue: #2f5d8e;
    --brand-green: #1f7a68;
    --ink-grey: #3a3a3a;
    --card-white: #ffffff;
  }
  * { box-sizing: border-box; margin: 0; padding: 0; }
  html, body { width: 1200px; height: 900px; overflow: hidden; }
  body {
    background: var(--page-bg);
    font-family: "Roboto", Arial, sans-serif;
    display: flex;
    flex-direction: column;
    align-items: center;
    justify-content: center;
    gap: 36px;
  }
  .card {
    width: 700px;
    height: 400px;
    position: relative;
    box-shadow: 0 6px 18px rgba(0,0,0,0.18);
    overflow: hidden;
  }

  /* Front */
  .card-front {
    background: linear-gradient(120deg, var(--teal-deep) 0%, var(--teal-mid) 50%, var(--navy-blue) 100%);
    color: var(--card-white);
  }
  .front-brand {
    position: absolute;
    top: 120px;
    left: 0; right: 0;
    display: flex;
    align-items: center;
    justify-content: center;
    gap: 16px;
  }
  .brand-square {
    width: 22px; height: 22px;
    background: var(--card-white);
  }
  .front-brand .brand-name {
    font-size: 44px;
    font-weight: 700;
    letter-spacing: 6px;
    text-transform: uppercase;
    color: var(--card-white);
  }
  .tagline-row {
    position: absolute;
    left: 0; right: 0;
    top: 260px;
    display: flex;
    align-items: center;
    gap: 14px;
  }
  .tagline-rule {
    flex: 1;
    height: 1.5px;
    background: rgba(255,255,255,0.85);
  }
  .tagline {
    font-size: 17px;
    font-weight: 400;
    letter-spacing: 0.3px;
    white-space: nowrap;
  }

  /* Back */
  .card-back { background: var(--card-white); }
  .back-brand {
    position: absolute;
    top: 70px;
    left: 210px;
    display: flex;
    align-items: center;
    gap: 10px;
  }
  .back-brand .brand-square { background: var(--brand-blue); width: 16px; height: 16px; }
  .back-brand .brand-name {
    font-size: 26px;
    font-weight: 700;
    letter-spacing: 3px;
    text-transform: uppercase;
    color: var(--brand-blue);
  }
  .services {
    position: absolute;
    top: 170px;
    right: 408px;
    list-style: none;
    text-align: right;
  }
  .services li {
    font-size: 19px;
    color: var(--brand-blue);
    line-height: 30px;
    display: flex;
    align-items: center;
    justify-content: flex-end;
    gap: 10px;
  }
  .services li::after {
    content: "";
    width: 16px; height: 16px;
    background: var(--brand-green);
  }
  .divider {
    position: absolute;
    left: 320px;
    top: 150px;
    width: 1.5px;
    height: 140px;
    background: var(--brand-blue);
  }
  .contact {
    position: absolute;
    left: 345px;
    top: 130px;
  }
  .contact-name {
    font-size: 26px;
    font-weight: 700;
    color: var(--brand-blue);
  }
  .credentials {
    font-size: 15px;
    color: var(--ink-grey);
    margin-top: 4px;
    margin-bottom: 14px;
  }
  .contact-list { list-style: none; }
  .contact-list li {
    display: flex;
    align-items: center;
    gap: 10px;
    font-size: 16px;
    color: var(--ink-grey);
    height: 30px;
  }
  .contact-icon {
    width: 24px; height: 24px;
    background: var(--brand-blue);
    display: flex; align-items: center; justify-content: center;
  }
</style>
</head>
<body>
  <section class="card card-front" aria-label="Card front">
    <div class="front-brand">
      <span class="brand-square"></span>
      <span class="brand-name">Varden Therapy</span>
    </div>
    <div class="tagline-row">
      <span class="tagline-rule"></span>
      <span class="tagline">Mobile Physiotherapy - Your Road To Recovery</span>
      <span class="tagline-rule"></span>
    </div>
  </section>

  <section class="card card-back" aria-label="Card back">
    <div class="back-brand">
      <span class="brand-square"></span>
      <span class="brand-name">Varden Therapy</span>
    </div>

    <ul class="services">
      <li>IMS</li>
      <li>Acupuncture</li>
      <li>Physiotherapy</li>
    </ul>

    <span class="divider"></span>

    <div class="contact">
      <div class="contact-name">Luke Varden</div>
      <div class="credentials">BSc(kin), MPT, CAFCI, IMS</div>
      <ul class="contact-list">
        <li>
          <span class="contact-icon">
            <svg width="14" height="14" viewBox="0 0 24 24" aria-hidden="true"><path fill="#fff" d="M6.6 10.8a15 15 0 0 0 6.6 6.6l2.2-2.2c.3-.3.7-.4 1-.2 1.1.4 2.3.6 3.6.6.6 0 1 .4 1 1V20c0 .6-.4 1-1 1A17 17 0 0 1 3 4c0-.6.4-1 1-1h3.5c.6 0 1 .4 1 1 0 1.3.2 2.5.6 3.6.1.3 0 .7-.2 1z"/></svg>
          </span>
          867-555-0142
        </li>
        <li>
          <span class="contact-icon">
            <svg width="14" height="14" viewBox="0 0 24 24" aria-hidden="true"><rect x="2" y="5" width="20" height="14" fill="none" stroke="#fff" stroke-width="2"/><path d="M2 5l10 8 10-8" fill="none" stroke="#fff" stroke-width="2"/></svg>
          </span>
          VardenTherapy@postnest.ca
        </li>
        <li>
          <span class="contact-icon">
            <svg width="14" height="14" viewBox="0 0 24 24" aria-hidden="true"><circle cx="12" cy="12" r="9" fill="none" stroke="#fff" stroke-width="2"/><ellipse cx="12" cy="12" rx="4" ry="9" fill="none" stroke="#fff" stroke-width="2"/><path d="M3 12h18" stroke="#fff" stroke-width="2"/></svg>
          </span>
          www.VardenTherapy.ca
        </li>
      </ul>
    </div>
  </section>
</body>
</html>
```